Bref créative
Harbor Floors & More --- Business card
Harbor Floors & More - thousands of types of tiles
Simple
Mira Dolent
4215 Varnell Rd,
Unit 3B, Concord, ON
L4K 9P7
mira.dolent@harborfloorsmore.example
www.harborfloorsmore.example
Introduction : Harbor Floors & More imports and distributes thousands of types of tiles in limestone, marble, slate, granite, porcelan, ceramic, glass and aluminum for homeowners, builders and contractors. Also providing custom-made solid wood kitchen cabinet and vanities.
the logo of Harbor Floors & More
Logo on Black
Logo on White

```html
<!DOCTYPE html>
<html lang="en">
<head>
<meta charset="utf-8">
<title>Harbor Floors &amp; More — Stationery</title>
<link rel="stylesheet" href="https://fonts.googleapis.com/css2?family=Questrial&display=swap">
<style>
:root{
  --bg:#eef0f1;
  --ink:#0b0b0c;
  --blue:#1ba3e0;
  --blue-light:#8fd6f4;
  --lime:#b7d433;
  --paper:#ffffff;
  --grey:#8a8f94;
}
*{box-sizing:border-box;margin:0;padding:0}
html,body{width:1200px;height:936px;overflow:hidden;background:var(--bg);font-family:"Questrial",sans-serif}
.canvas{position:relative;width:1200px;height:936px}
.piece{position:absolute;background:var(--paper);overflow:hidden;box-shadow:0 2px 8px rgba(0,0,0,.12)}
.piece svg.band{position:absolute;left:0;width:100%;display:block}
.brand{position:absolute;color:var(--paper);text-transform:uppercase;letter-spacing:.02em;line-height:1.05;white-space:nowrap}
.brand .mark{display:inline-block;width:.8em;height:.8em;background:var(--blue);margin-right:.35em;vertical-align:-.05em}
.small{position:absolute;color:var(--paper);font-size:5px;line-height:1.4;white-space:nowrap}

.letterhead{left:46px;top:38px;width:304px;height:530px}
.letterhead .brand{left:18px;top:22px;font-size:11px}
.letterhead .small{left:205px;top:14px}
.letterhead .watermark{position:absolute;left:0;right:0;top:215px;text-align:center;font-size:22px;color:#cfe9f5;text-transform:uppercase}

.folder{left:635px;top:38px;width:508px;height:584px}
.folder .brand{left:0;right:0;top:265px;text-align:center;font-size:34px}
.folder .brand .sub{display:block;font-size:21px;margin-top:4px}
.folder .url{position:absolute;left:0;right:0;bottom:24px;text-align:center;color:var(--paper);font-size:9px;letter-spacing:.12em}

.card-front{left:38px;top:655px;width:203px;height:87px}
.card-front .brand{left:14px;top:12px;font-size:9px}
.card-front .small{left:14px;top:40px;color:var(--paper)}
.card-front .name{position:absolute;right:14px;top:40px;color:var(--lime);font-size:6px}
.card-back{left:38px;top:775px;width:203px;height:101px}
.card-back .brand{left:0;right:0;top:36px;text-align:center;color:var(--ink);font-size:10px}
.card-back .url{position:absolute;left:0;right:0;bottom:12px;text-align:center;color:var(--grey);font-size:6px}

.envelope-small{left:267px;top:673px;width:406px;height:203px}
.envelope-small .brand{left:22px;top:20px;font-size:11px}
.envelope-small .small{left:250px;top:18px}

.envelope-large{left:724px;top:673px;width:432px;height:203px}
.envelope-large .url{position:absolute;left:0;right:0;top:18px;text-align:center;color:var(--paper);font-size:8px;letter-spacing:.12em}
</style>
</head>
<body>
<main class="canvas">

  <section class="piece letterhead" aria-label="Letterhead">
    <svg class="band" style="top:0;height:80px" viewBox="0 0 304 80" preserveAspectRatio="none">
      <path d="M0 0H304V44Q150 74 0 46Z" fill="var(--ink)"/>
      <path d="M0 46Q150 74 304 44V52Q150 84 0 56Z" fill="var(--blue)"/>
    </svg>
    <div class="brand"><span class="mark"></span>Harbor Floors &amp; More</div>
    <div class="small">4215 Varnell Rd,<br>Unit 3B, Concord, ON<br>L4K 9P7</div>
    <div class="watermark">Harbor Floors &amp; More</div>
  </section>

  <section class="piece folder" aria-label="Presentation folder">
    <svg class="band" style="top:0;height:584px" viewBox="0 0 508 584" preserveAspectRatio="none">
      <rect width="508" height="584" fill="var(--paper)"/>
      <path d="M0 0H508V478Q250 440 0 500Z" fill="var(--ink)"/>
      <path d="M0 500Q250 440 508 478V492Q250 452 0 512Z" fill="var(--lime)"/>
      <path d="M0 516Q250 458 508 498V584H0Z" fill="var(--blue)"/>
    </svg>
    <div class="brand"><span class="mark"></span>Harbor Floors<span class="sub">&amp; More</span></div>
    <div class="url">www.harborfloorsmore.example</div>
  </section>

  <section class="piece card-front" aria-label="Business card front">
    <svg class="band" style="top:0;height:87px" viewBox="0 0 203 87" preserveAspectRatio="none">
      <path d="M0 0H203V62Q100 80 0 64Z" fill="var(--ink)"/>
      <path d="M0 64Q100 80 203 62V87H0Z" fill="var(--blue)"/>
    </svg>
    <div class="brand"><span class="mark"></span>Harbor Floors &amp; More</div>
    <div class="small">4215 Varnell Rd, Unit 3B<br>mira.dolent@harborfloorsmore.example</div>
    <div class="name">Mira Dolent</div>
  </section>

  <section class="piece card-back" aria-label="Business card back">
    <svg class="band" style="bottom:0;height:30px" viewBox="0 0 203 30" preserveAspectRatio="none">
      <path d="M0 10Q100 0 203 12V30H0Z" fill="var(--ink)"/>
    </svg>
    <div class="brand"><span class="mark"></span>Harbor Floors &amp; More</div>
  </section>

  <section class="piece envelope-small" aria-label="Envelope">
    <svg class="band" style="top:0;height:80px" viewBox="0 0 406 80" preserveAspectRatio="none">
      <path d="M0 0H406V46Q200 72 0 50Z" fill="var(--ink)"/>
      <path d="M0 50Q200 72 406 46V54Q200 82 0 58Z" fill="var(--blue)"/>
    </svg>
    <div class="brand"><span class="mark"></span>Harbor Floors &amp; More</div>
    <div class="small">4215 Varnell Rd, Unit 3B,<br>Concord, ON L4K 9P7</div>
  </section>

  <section class="piece envelope-large" aria-label="Envelope back">
    <svg class="band" style="top:0;height:203px" viewBox="0 0 432 203" preserveAspectRatio="none">
      <path d="M0 0H432V44Q216 68 0 50Z" fill="var(--blue)"/>
      <path d="M0 50Q216 68 432 44V52Q216 78 0 58Z" fill="var(--blue-light)"/>
      <path d="M0 58L216 140L432 52" fill="none" stroke="#dfe3e6" stroke-width="1"/>
    </svg>
    <div class="url">www.harborfloorsmore.example</div>
  </section>

</main>
</body>
</html>
```